Sell the dream! Property investment proposal document

We are looking for a proposal document which outlines our vision for property development. The purpose of the document is to raise investment from investors - sell the dream!
Brief summary:
Kestrel Dwellings Developments, is an emerging New Zealand property investment company with a focus on providing unique property investment opportunities.
Our expertise and capabilities in architectural modular homes provide us with a remarkable advantage in tackling the development of properties that are typically considered challenging, remote, or uniquely positioned.
Our specialization in this niche sector of property development not only sets us apart from competitors, but also paves the way for lucrative investment opportunities in the New Zealand property market.
Feel free to use any images from www.kestreldwellings.co.nz
Target Market(s)
investors for a unique property development opportunity
Industry/Entity Type
luxury property development in unique locations throughout New Zealand
Colors
Designer to choose only greyscale colors for use in the design.
Look and feel

```html
<!DOCTYPE html>
<html lang="en">
<head>
<meta charset="utf-8">
<title>Kestrel Dwellings – Investment Proposal Spreads</title>
<link href="https://fonts.googleapis.com/css2?family=Bitter:wght@600&family=Inter:wght@400;500&display=swap" rel="stylesheet">
<style>
:root{
  --backdrop:#6a6a6a;
  --page:#2e2e2e;
  --page-deep:#262626;
  --band:#383838;
  --paper:#f2f2f2;
  --ink-light:#f4f4f4;
  --ink-soft:#cfcfcf;
  --ink-dark:#111;
}
*{margin:0;padding:0;box-sizing:border-box}
html,body{width:1200px;height:663px;overflow:hidden;background:var(--backdrop)}
.canvas{position:relative;width:1200px;height:663px}
.spread{position:absolute;width:336px;height:263px;background:var(--page);overflow:hidden}
.spread::after{content:"";position:absolute;left:167px;top:0;width:2px;height:100%;background:linear-gradient(90deg,rgba(0,0,0,.35),rgba(255,255,255,.06))}
.abs{position:absolute}
.photo{position:absolute}
.strip{position:absolute;background:var(--paper)}
.heading{position:absolute;font-family:"Bitter",serif;font-weight:600;color:var(--ink-light);font-size:15px;line-height:1.02;letter-spacing:.4px;text-transform:uppercase}
.heading.center{text-align:center}
.body-copy{position:absolute;font-family:"Inter",sans-serif;font-size:3.1px;line-height:1.32;color:var(--ink-soft)}
.body-copy p+p{margin-top:3px}
.url{position:absolute;font-family:"Inter",sans-serif;font-size:3.6px;color:var(--ink-soft);bottom:9px}
.url.dark{color:var(--ink-dark)}
.brand-mark{position:absolute;bottom:8px;display:flex;align-items:center;gap:2px;font-family:"Inter",sans-serif;font-weight:500;font-size:4.2px;color:var(--ink-light)}
.brand-mark i{display:block;width:4px;height:4px;background:var(--ink-light)}
.cover-title{position:absolute;font-family:"Inter",sans-serif;font-weight:500;font-size:34px;letter-spacing:-1.5px;color:var(--ink-dark);line-height:1}
.cover-tagline{position:absolute;font-family:"Bitter",serif;font-weight:600;font-size:10.5px;color:var(--ink-light);letter-spacing:.3px}
</style>
</head>
<body>
<main class="canvas">

  <!-- Cover spread -->
  <section class="spread cover" style="left:55px;top:47px">
    <div class="photo" role="img" aria-label="Dark cantilevered modular home on a grassy hillside with a boulder, overlooking the sea" style="left:93px;top:0;width:243px;height:227px;background:linear-gradient(180deg,#eceeee 0%,#dfe3e4 30%,#4a4d4c 45%,#59684a 62%,#6f8a3d 80%,#5d7a2f 100%)"></div>
    <h1 class="cover-title" style="left:150px;top:20px">Kestrel</h1>
    <p class="cover-tagline" style="left:198px;top:203px">SELL THE DREAM!</p>
    <span class="url" style="left:16px">www.kestreldwellings.co.nz</span>
    <span class="url" style="left:184px">www.kestreldwellings.co.nz</span>
    <span class="brand-mark" style="left:292px"><i></i>Kestrel Dwellings</span>
  </section>

  <!-- Business overview -->
  <section class="spread overview" style="left:431px;top:47px">
    <div class="strip" style="left:0;top:0;width:8px;height:12px"></div>
    <div class="strip" style="left:0;top:195px;width:8px;height:68px"></div>
    <div class="abs" style="left:8px;top:0;width:328px;height:19px;background:var(--page-deep)"></div>
    <div class="photo" role="img" aria-label="Glass pavilion home at sunset facing a calm bay" style="left:0;top:19px;width:230px;height:166px;background:linear-gradient(180deg,#8e8a80 0%,#d9c79a 35%,#b8a27a 55%,#6d6a62 75%,#4a4743 100%)"></div>
    <h2 class="heading" style="left:242px;top:77px">Business<br>Overview</h2>
    <div class="body-copy" style="left:242px;top:119px;width:85px">
      <p>Kestrel Dwellings Developments, is an emerging New Zealand property investment company with a focus on providing unique property investment opportunities.</p>
      <p>Our expertise and capabilities in architectural modular homes provide us with a remarkable advantage in tackling the development of properties that are typically considered challenging, remote, or uniquely positioned.</p>
      <p>As a company, with 48 employees boasting a wealth of experience in handling complex architectural projects, making us well-equipped to navigate the intricacies and demands of such ventures.</p>
      <p>This advantage allows us to not only execute projects efficiently but also to deliver exceptional results within condensed time frames.</p>
    </div>
    <div class="body-copy" style="left:178px;top:205px;width:52px">
      <p>By capitalizing on our ability to develop difficult, remote, or one-of-a-kind properties swiftly and effectively, Kestrel Dwellings Developments offers investors a rare chance to engage in projects that promise exceptional profitability in the New Zealand property market.</p>
    </div>
    <div class="body-copy" style="left:242px;top:205px;width:66px">
      <p>Our specialization in this niche sector of property development not only sets us apart from competitors, but also paves the way for lucrative investment opportunities in the New Zealand property market.</p>
    </div>
    <span class="url" style="left:16px">www.kestreldwellings.co.nz</span>
    <span class="brand-mark" style="left:120px"><i></i>Kestrel Dwellings</span>
    <span class="url" style="left:292px">www.kestreldwellings.co.nz</span>
  </section>

  <!-- Business origins -->
  <section class="spread origins" style="left:806px;top:47px">
    <div class="strip" style="left:0;top:0;width:40px;height:8px"></div>
    <div class="strip" style="left:296px;top:0;width:40px;height:8px"></div>
    <div class="abs" style="left:40px;top:0;width:11px;height:161px;background:#1c1c1c"></div>
    <div class="photo" role="img" aria-label="Minimal interior with lounge chairs before a floor-to-ceiling window over the ocean" style="left:51px;top:0;width:233px;height:161px;background:linear-gradient(180deg,#e9eef2 0%,#b9cbd8 30%,#4f7ea3 48%,#5d5146 62%,#2a211c 80%,#3a2e26 100%)"></div>
    <div class="abs" style="left:284px;top:0;width:12px;height:161px;background:#1c1c1c"></div>
    <h2 class="heading center" style="left:34px;top:184px;width:100px">Business<br>Origins</h2>
    <div class="body-copy" style="left:179px;top:178px;width:68px">
      <p>Kestrel Dwellings Developments was established with the goal of transforming the property investment market in New Zealand by introducing an innovative approach that centers on architectural modular designs and streamlined project timelines.</p>
      <p>Driven by our enthusiasm for architecture and real estate, we have expanded our successful business model to not only offer financial opportunities for investors but also to expand on our passion for high-end architectural design.</p>
    </div>
    <div class="body-copy" style="left:261px;top:178px;width:66px">
      <p>With a wealth of experience accumulated over the past six years in the construction and the property market, we are pivoting to focus solely on our property development initiatives, presenting completed Kestrel projects to the market, in exclusive locations.</p>
      <p>These projects will boast high-quality standards, meticulous attention to detail and landscaping, and creative design elements.</p>
    </div>
    <span class="url" style="left:8px">www.kestreldwellings.co.nz</span>
    <span class="brand-mark" style="left:124px"><i></i>Kestrel Dwellings</span>
    <span class="url" style="left:292px">www.kestreldwellings.co.nz</span>
  </section>

  <!-- Market approach -->
  <section class="spread approach" style="left:55px;top:350px">
    <div class="body-copy" style="left:12px;top:16px;width:56px">
      <p>By introducing completed Kestrel properties into the market, we aim to reach a wider audience, catering to individuals who prefer ready-to-occupy homes, over engaging in the design and construction process.</p>
      <p>This approach also simplifies the financing process for prospective buyers, as established properties are often preferred by financial lenders.</p>
    </div>
    <div class="photo" role="img" aria-label="Covered outdoor terrace of a dark modular home with grasses and a dining table" style="left:6px;top:69px;width:154px;height:158px;background:linear-gradient(180deg,#e4e4e2 0%,#d6d7d4 25%,#2b2c2b 40%,#4b4f48 65%,#8f8c6a 85%,#9c9a92 100%)"></div>
    <div class="photo" role="img" aria-label="Black timber-clad two-storey modular home among trees with a paved entry" style="left:167px;top:0;width:169px;height:263px;background:linear-gradient(180deg,#c9cbcb 0%,#7f8b74 22%,#262826 45%,#1f2120 65%,#5c6656 80%,#cfd0cd 100%)"></div>
    <span class="url" style="left:16px">www.kestreldwellings.co.nz</span>
    <span class="brand-mark" style="left:122px"><i></i>Kestrel Dwellings</span>
    <span class="url" style="left:292px">www.kestreldwellings.co.nz</span>
  </section>

  <!-- Competitive advantage -->
  <section class="spread advantage" style="left:431px;top:350px">
    <h2 class="heading center" style="left:0;top:18px;width:168px">Competitive<br>Advantage</h2>
    <div class="photo" role="img" aria-label="Living room with glass wall overlooking green hills and a harbour" style="left:0;top:64px;width:168px;height:165px;background:linear-gradient(180deg,#e0e6ea 0%,#b9c4cc 22%,#5c6f5d 40%,#8fa065 58%,#d3cfc4 72%,#8a7b68 88%,#5a4d40 100%)"></div>
    <div class="photo" role="img" aria-label="Interior with armchair and hide rug facing tall windows onto rocky mountains" style="left:174px;top:4px;width:155px;height:150px;background:linear-gradient(180deg,#8d8c82 0%,#a59a84 30%,#4a4640 55%,#bdbdb8 75%,#6f6a64 100%)"></div>
    <div class="body-copy" style="left:183px;top:174px;width:58px">
      <p>Our competitive advantage lies in the uniqueness of our property investment opportunities.</p>
      <p>Unlike traditional real estate companies, we focus on offering properties that are not only profitable but also aesthetically pleasing and unique.</p>
    </div>
    <div class="body-copy" style="left:261px;top:174px;width:62px">
      <p>By catering to the tastes of architecture lovers, we set ourselves apart from the competition and attract a niche market of customers who appreciate the artistry and design of our projects.</p>
      <p>Additionally, the streamlined and condensed timelines facilitated by our modular approach provide quicker returns on investment.</p>
    </div>
    <div class="strip" style="left:169px;top:229px;width:167px;height:34px"></div>
    <span class="url" style="left:16px">www.kestreldwellings.co.nz</span>
    <span class="brand-mark" style="left:120px"><i></i>Kestrel Dwellings</span>
    <span class="url dark" style="left:292px">www.kestreldwellings.co.nz</span>
  </section>

  <!-- Financial summary -->
  <section class="spread financial" style="left:806px;top:350px">
    <h2 class="heading" style="left:45px;top:41px">Financial<br>Summary</h2>
    <div class="body-copy" style="left:199px;top:21px;width:46px">
      <p>In terms of financial projections, with each development, we anticipate a profit of 10%-20% which will be project dependent.</p>
      <p>This growth is fueled by the increasing demand for unique property investments in New Zealand and our ability to deliver high-quality services to the market in a condensed time frame, with heavily controlled costs.</p>
      <p>With a solid business model and a dedicated team, we are confident in our ability to achieve success and establish Kestrel Dwellings Investments as a trusted name in the industry.</p>
    </div>
    <div class="body-copy" style="left:266px;top:21px;width:48px">
      <p>New Zealand's property market has been experiencing steady growth over the years, making it an attractive destination for property investors.</p>
      <p>With its beautiful landscapes and strong economy, New Zealand offers a diverse range of investment opportunities for both local and international investors.</p>
      <p>The demand for quality properties in prime locations continues to rise, creating a favorable environment for property investment companies like ours that can lean on our modular benefits of being able to reach unique and remote locations.</p>
    </div>
    <div class="photo" role="img" aria-label="Aerial view of a low modular home on rolling farmland beside the sea at dusk" style="left:0;top:113px;width:336px;height:150px;background:linear-gradient(180deg,#6e6a5c 0%,#8a8167 18%,#4d4a2e 35%,#5b5426 60%,#4a4420 80%,#3a351c 100%)"></div>
    <span class="url" style="left:8px">www.kestreldwellings.co.nz</span>
    <span class="brand-mark" style="left:124px"><i></i>Kestrel Dwellings</span>
    <span class="url" style="left:292px">www.kestreldwellings.co.nz</span>
  </section>

</main>
</body>
</html>
```